Tamarind Lodgings letterhead

We need a letterhead designed that includes the new logo that has just been designed for our business. The letterhead will need to be formatted for digital use as well as for print.

Target Market(s)

Private tenant, corporate tenants, real estate agents

Industry/Entity Type

Digital

Requirements
Must have
• ABN 87 504 912 386
PO Box 7816, Harlowe Mail Centre QLD 4790
Email: linus.pardoe@quillmail.example
Ph: 0438 617 209

```html
<!DOCTYPE html>
<html lang="en">
<head>
<meta charset="utf-8">
<title>Tamarind Lodgings Letterhead</title>
<link rel="stylesheet" href="https://fonts.googleapis.com/css2?family=Comfortaa:wght@500;700&display=swap">
<style>
  :root {
    --paper: #ffffff;
    --plum: #5c0b26;
    --rust: #7b2a24;
    --ink-light: #ffffff;
  }
  html, body {
    margin: 0;
    padding: 0;
    overflow: hidden;
    background: var(--paper);
  }
  .letterhead {
    position: relative;
    width: 849px;
    height: 1200px;
    background: var(--paper);
    overflow: hidden;
    font-family: "Comfortaa", sans-serif;
  }
  .brand {
    position: absolute;
    top: 35px;
    left: 252px;
    display: flex;
    align-items: center;
    gap: 16px;
  }
  .brand-square {
    width: 102px;
    height: 108px;
    border-radius: 12px;
    background: var(--plum);
  }
  .brand-name {
    margin: 0;
    color: var(--rust);
    font-weight: 700;
    font-size: 34px;
    line-height: 1.05;
    letter-spacing: 1px;
    text-transform: uppercase;
  }
  .footer-arc {
    position: absolute;
    left: 0;
    bottom: 0;
    width: 849px;
    height: 175px;
  }
  .contact {
    position: absolute;
    left: 287px;
    top: 1051px;
    margin: 0;
    color: var(--ink-light);
    font-weight: 500;
    font-size: 18px;
    line-height: 25.5px;
    font-style: normal;
  }
</style>
</head>
<body>
  <main class="letterhead">
    <header class="brand">
      <div class="brand-square"></div>
      <h1 class="brand-name">Tamarind<br>Lodgings</h1>
    </header>

    <svg class="footer-arc" viewBox="0 1025 849 175" aria-hidden="true">
      <ellipse cx="430" cy="1330" rx="445" ry="300" fill="var(--plum)"/>
    </svg>

    <address class="contact">
      ABN 87 504 912 386<br>
      PO BOX 7816 , Harlowe Mail Centre<br>
      QLD 4790<br>
      EMAIL : linus.pardoe@quillmail.example<br>
      PHONE : 0438 617 209
    </address>
  </main>
</body>
</html>
```